10 Labels for Wild Bird Food

Label Design Request for New Products
We are excited to announce the launch of 10 new products and are seeking vibrant, fun, and colorful labels to match their energy. Each label should measure 6 x 4 inches (152.4mm x 101.6mm) and must feature our brand logo. Additionally, please include all the necessary information as detailed in the attached Word document.

Let's make our products stand out on the shelves with eye-catching designs!

Target Market(s)

Wild Bird Food Buyers

Requirements
Must have
• Logo

```html
<!DOCTYPE html>
<html lang="en">
<head>
<meta charset="utf-8">
<title>Peanut Granules 5L Bag – Label</title>
<link href="https://fonts.googleapis.com/css2?family=Outfit:wght@300;400;500;600;700&display=swap" rel="stylesheet">
<style>
  :root {
    --orange: #cc6c0a;
    --green: #8cbc1c;
    --teal: #138a80;
    --white: #ffffff;
    --page: #f1f2f2;
  }
  * { margin: 0; padding: 0; box-sizing: border-box; }
  html, body { width: 1200px; height: 1200px; overflow: hidden; }
  body {
    background: var(--page);
    font-family: "Outfit", sans-serif;
    position: relative;
  }
  .label {
    position: absolute;
    left: 202px; top: 334px;
    width: 796px; height: 531px;
    background: var(--orange);
    border-radius: 38px;
    overflow: hidden;
    color: var(--white);
  }
  .product-visual {
    position: absolute;
    left: 240px; top: 70px;
    width: 460px; height: 380px;
    border-radius: 50%;
    background: radial-gradient(ellipse at center, rgba(230,150,60,0.55) 0%, rgba(210,120,30,0.3) 45%, rgba(204,108,10,0) 72%);
  }
  .brand {
    position: absolute;
    left: 0; right: 0; top: 62px;
    display: flex; justify-content: center; align-items: center; gap: 12px;
  }
  .brand-dot {
    width: 34px; height: 34px; border-radius: 50%;
    background: var(--teal);
  }
  .brand-name {
    font-weight: 700; font-size: 44px; color: var(--green);
    letter-spacing: 0.5px; line-height: 1;
  }
  .product-title {
    position: absolute;
    left: 0; right: 0; top: 152px;
    text-align: center;
    font-weight: 600; font-size: 62px; letter-spacing: 0.6px;
    line-height: 1;
  }
  .copy {
    position: absolute;
    left: 48px; top: 250px; width: 378px;
  }
  .copy h2 {
    font-weight: 700; font-size: 12px; line-height: 14.5px;
    color: var(--green); text-transform: uppercase; letter-spacing: 0.1px;
  }
  .copy p {
    font-weight: 300; font-size: 12px; line-height: 14.5px;
    letter-spacing: 0.1px;
    text-align: justify; margin-top: 4px;
  }
  .copy h2.usage { margin-top: 14px; }
  .details {
    position: absolute;
    left: 457px; top: 246px; width: 287px;
    text-align: center;
  }
  .net-weight { font-weight: 500; font-size: 12.5px; }
  .code-panel {
    margin-top: 6px; height: 118px;
    background: var(--white); border-radius: 18px;
  }
  .batch-panel {
    margin-top: 13px; height: 41px;
    background: var(--white); border-radius: 9px;
    display: flex; align-items: center; justify-content: center;
    color: var(--orange); font-size: 11.5px; font-weight: 400; gap: 6px;
  }
  .batch-panel strong { font-weight: 600; }
  .warning { margin-top: 4px; font-size: 8px; font-weight: 600; }
  .footer-band {
    position: absolute;
    left: 0; right: 0; bottom: 0; height: 62px;
    background: var(--green);
  }
  .sku {
    position: absolute; left: 48px; top: 23px;
    font-size: 11px; font-weight: 500;
  }
  .contact {
    position: absolute; left: 0; right: 0; top: 18px;
    text-align: center; font-size: 9.5px; font-weight: 500; line-height: 13px;
  }
  .social {
    position: absolute; right: 44px; top: 13px;
    display: flex; gap: 4px;
  }
  .social span {
    width: 21px; height: 21px; border-radius: 50%;
    background: var(--white);
  }
</style>
</head>
<body>
  <main class="label">
    <div class="product-visual" role="img" aria-label="Pile of golden peanut granules"></div>

    <header class="brand">
      <span class="brand-dot"></span>
      <span class="brand-name">Bright Perch</span>
    </header>

    <h1 class="product-title">Peanut Granules 5L Bag</h1>

    <section class="copy">
      <h2>Nourish your garden birds with delicious, nutritious peanut granules!</h2>
      <p>Transform your garden into a vibrant bird sanctuary with our Peanut Granules 5L Bag, the perfect choice for bird enthusiasts who want to provide their avian visitors with a high-energy, nutrient-rich treat. Ideal for a wide variety of bird species, these premium peanut granules are sure to make your garden a favorite feeding spot.</p>
      <h2 class="usage">Easy to use:</h2>
      <p>Fill your bird feeders, sprinkle on bird tables, or mix with other bird food to create an irresistible feast for your garden birds. Watch as they flock to your garden, bringing vibrant colors and joyful chirping to your outdoor space.</p>
    </section>

    <aside class="details">
      <div class="net-weight">Net Weight: 2800g</div>
      <div class="code-panel"></div>
      <div class="batch-panel">
        <span><strong>EXPIRY DATE:</strong> 00/000</span>
        <span>|</span>
        <span><strong>BATCH:</strong> 0000</span>
      </div>
      <div class="warning">Not for human consumption &nbsp;|&nbsp; May Contain Nuts</div>
    </aside>

    <footer class="footer-band">
      <div class="sku">BP14</div>
      <div class="contact">
        Marlow Supplies, Oakfield Trade Park, Farnley, FN12 4RT<br>
        sales@marlowsupplies.co.uk
      </div>
      <div class="social"><span></span><span></span><span></span></div>
    </footer>
  </main>
</body>
</html>
```